Book Cover Design RTM

Want a new book cover but want to use the same photo and change the sub name. This is for a brand called "Amber Meadow Living". The book is called "Quiet Steps, Bright Days"

This is for a 8.5 * 11 book size

We really want to brand the Amber Meadow Living

I've attached a sample of an old book cover, the photo I want used and the amber meadow living logo

Requirements
Must have
• Must have the logo,

must have the book title. "Quiet Steps, Bright Days"

Must have "Featuring" The Amber Meadow Living Tumble Card Game"

On the back put the logo and Amber Meadow Living Nutrition

must have the authors name "Norma Plaskett" on the page

"The Golden Stride Map"
Nice to have
• Amber Meadow Living Presents:

the book title

```html
<!DOCTYPE html>
<html lang="en">
<head>
<meta charset="utf-8">
<title>Quiet Steps, Bright Days — Book Cover</title>
<link rel="stylesheet" href="https://fonts.googleapis.com/css2?family=Bebas+Neue&family=Montserrat:wght@400;700&family=Oswald:wght@400;500&display=swap">
<style>
  :root{
    --bg:#14302f;
    --ink:#000000;
    --paper:#ffffff;
    --mint:#86dcc6;
    --frame:#d9d9d9;
    --skin:#7a4a33;
    --ball:#6fc4ad;
  }
  *{margin:0;padding:0;box-sizing:border-box}
  html,body{width:1200px;height:900px;overflow:hidden;background:var(--bg)}
  .canvas{position:relative;width:1200px;height:900px}
  .front-cover,.spine,.back-cover{position:absolute;top:144px;height:630px}
  .front-cover{left:204px;width:388px;background:var(--ink);overflow:hidden}
  .cover-photo{position:absolute;left:68px;top:12px;width:320px;height:618px;
    background:radial-gradient(ellipse 45% 40% at 35% 50%, var(--ball) 0%, rgba(111,196,173,.55) 55%, transparent 80%),
               radial-gradient(ellipse 30% 55% at 68% 45%, var(--skin) 0%, rgba(122,74,51,.4) 60%, transparent 85%),
               var(--ink)}
  .series{position:absolute;left:28px;top:58px;font-family:'Montserrat',sans-serif;color:var(--paper);font-size:16px;line-height:21px}
  .series strong{font-weight:700;display:block}
  .rule{position:absolute;height:2px;background:var(--mint)}
  .author{position:absolute;left:28px;top:134px;font-family:'Montserrat',sans-serif;color:var(--mint);font-size:20px}
  .brand{font-family:'Montserrat',sans-serif;font-weight:700;color:var(--paper);letter-spacing:2px;text-align:center;display:flex;align-items:center;gap:8px;justify-content:center}
  .brand .dot{width:10px;height:10px;border-radius:50%;background:var(--paper)}
  .front-brand{position:absolute;left:84px;top:278px;width:160px;font-size:13px;line-height:16px;color:var(--ink)}
  .front-brand .dot{background:var(--ink)}
  .book-title{position:absolute;left:26px;top:310px;font-family:'Bebas Neue',sans-serif;color:var(--paper);font-size:90px;line-height:90px;letter-spacing:-1px}
  .featuring{position:absolute;left:28px;top:514px;font-family:'Oswald',sans-serif;text-transform:uppercase}
  .featuring .label{color:var(--mint);font-weight:500;font-size:17px;line-height:22px}
  .featuring .line{color:var(--paper);font-size:15px;line-height:22px}
  .featuring .game{color:var(--mint);font-weight:500;font-size:20px;line-height:24px}
  .spine{left:592px;width:18px;background:var(--ink)}
  .spine-text{position:absolute;left:50%;white-space:nowrap;transform:translateX(-50%) rotate(-90deg);transform-origin:center;color:var(--paper)}
  .spine-brand{top:80px;font-family:'Montserrat',sans-serif;font-size:6px;letter-spacing:1px}
  .spine-title{top:300px;font-family:'Montserrat',sans-serif;font-weight:700;font-size:11px;letter-spacing:1px}
  .spine-author{top:545px;font-family:'Montserrat',sans-serif;font-size:8px;letter-spacing:2px}
  .back-cover{left:610px;width:386px;background:var(--frame)}
  .back-panel{position:absolute;left:18px;top:28px;width:350px;height:572px;background:var(--ink);text-align:center}
  .back-brand{margin-top:112px;font-size:18px}
  .affirmations{list-style:none;margin-top:48px;font-family:'Oswald',sans-serif;color:var(--paper);font-size:25px;line-height:36.8px;text-transform:uppercase}
</style>
</head>
<body>
<main class="canvas">
  <section class="front-cover">
    <div class="cover-photo" role="img" aria-label="Photo of the author in workout wear leaning on a mint exercise ball"></div>
    <p class="series">Your<strong>Golden Stride</strong>Map</p>
    <div class="rule" style="left:28px;top:117px;width:170px"></div>
    <p class="author">by NORMA PLASKETT</p>
    <div class="brand front-brand"><span class="dot"></span><span>AMBER MEADOW LIVING</span></div>
    <h1 class="book-title">Quiet Steps,<br>Bright Days</h1>
    <div class="rule" style="left:26px;top:500px;width:186px"></div>
    <div class="featuring">
      <p class="label">Featuring:</p>
      <p class="line">“The Amber Meadow Living</p>
      <p class="game">Tumble Card Game”</p>
    </div>
    <div class="rule" style="left:26px;top:576px;width:186px"></div>
  </section>

  <section class="spine">
    <span class="spine-text spine-brand">AMBER MEADOW LIVING</span>
    <span class="spine-text spine-title">QUIET STEPS BRIGHT DAYS</span>
    <span class="spine-text spine-author">NORMA PLASKETT</span>
  </section>

  <section class="back-cover">
    <div class="back-panel">
      <div class="brand back-brand"><span class="dot"></span><span>AMBER MEADOW LIVING</span></div>
      <ul class="affirmations">
        <li>I crush my goals</li>
        <li>I persever</li>
        <li>I take decsive action</li>
        <li>I am deliberate</li>
        <li>I hold my head high</li>
        <li>I don’t quit</li>
        <li>I am formidable</li>
        <li>I am secure</li>
        <li>I am motivated</li>
        <li>I am loved</li>
      </ul>
    </div>
  </section>
</main>
</body>
</html>
```